Business card por a urban DJ, up scale audience target

Need a sober design, modern, conservative colors but i can consider some options, y play rnb, hip hop, EDM and top40.

Business card for contact and personal info, double sided, use logo attrached please; im 42 so i need a card acording to my age an target audience.

Target Market(s)

Adult people, up scale audience

Industry/Entity Type

Music Download

Contact Information for Business Card

Cel (318) 4207265518 www.lumadrift.com

Requirements
Must have
• open mind
Nice to have
• open mind
Should not have
• DJ

```html
<!DOCTYPE html>
<html lang="en">
<head>
<meta charset="utf-8">
<title>Lumadrift Business Card</title>
<link href="https://fonts.googleapis.com/css2?family=Arimo:wght@400;700&display=swap" rel="stylesheet">
<style>
  :root {
    --page-bg: #e7e6e3;
    --card-white: #ffffff;
    --card-shade: #e9e9e9;
    --card-black: #161616;
    --card-black-soft: #2a2a2a;
    --ink: #1b1b1b;
    --ink-grey: #555555;
    --band-text: #e6e6e6;
    --band-sub: #c4c4c4;
    --logo-light: #e4e4e4;
  }
  * { margin: 0; padding: 0; box-sizing: border-box; }
  html, body {
    width: 1200px;
    height: 950px;
    overflow: hidden;
    background: var(--page-bg);
    font-family: "Arimo", Arial, sans-serif;
  }
  .canvas {
    position: relative;
    width: 1200px;
    height: 950px;
  }
  .card {
    position: absolute;
    left: 240px;
    width: 720px;
    height: 411px;
    overflow: hidden;
    box-shadow: 0 8px 24px rgba(0, 0, 0, 0.18);
  }

  /* Front side */
  .card--front {
    top: 50px;
    background: linear-gradient(170deg, var(--card-white) 45%, var(--card-shade) 100%);
  }
  .brand {
    position: absolute;
    left: 56px;
    top: 66px;
  }
  .brand__name {
    font-weight: 700;
    font-size: 92px;
    line-height: 1;
    letter-spacing: 2px;
    color: var(--ink);
  }
  .contact {
    position: absolute;
    left: 58px;
    top: 236px;
    list-style: none;
  }
  .contact__item {
    display: flex;
    align-items: center;
    gap: 12px;
    font-size: 21px;
    color: var(--ink-grey);
    line-height: 1;
    margin-bottom: 12px;
  }
  .contact__icon {
    width: 18px;
    height: 20px;
    flex: none;
  }
  .name-band {
    position: absolute;
    right: 0;
    bottom: 56px;
    width: 300px;
    height: 76px;
  }
  .name-band svg {
    position: absolute;
    inset: 0;
  }
  .name-band__text {
    position: absolute;
    left: 100px;
    top: 14px;
    color: var(--band-text);
  }
  .name-band__name {
    font-size: 23px;
    font-weight: 700;
    letter-spacing: 1px;
    line-height: 1.1;
  }
  .name-band__title {
    font-size: 19px;
    letter-spacing: 1px;
    color: var(--band-sub);
    margin-top: 3px;
  }

  /* Back side */
  .card--back {
    top: 501px;
    background: linear-gradient(100deg, var(--card-black) 0%, var(--card-black) 62%, var(--card-black-soft) 74%, var(--card-black) 86%);
  }
  .back-brand {
    position: absolute;
    left: 0;
    right: 0;
    top: 122px;
    text-align: center;
  }
  .back-brand__name {
    font-weight: 700;
    font-size: 112px;
    line-height: 1;
    letter-spacing: 3px;
    color: var(--logo-light);
  }
  .back-web {
    position: absolute;
    right: 170px;
    top: 250px;
    font-size: 21px;
    letter-spacing: 2px;
    color: var(--logo-light);
  }
</style>
</head>
<body>
<main class="canvas">

  <section class="card card--front" aria-label="Card front">
    <div class="brand">
      <span class="brand__name">LUMA</span>
    </div>

    <ul class="contact">
      <li class="contact__item">
        <svg class="contact__icon" viewBox="0 0 18 20" aria-hidden="true">
          <rect x="4" y="1" width="10" height="18" rx="2" fill="none" stroke="#1b1b1b" stroke-width="2"/>
          <rect x="7" y="15" width="4" height="2" fill="#1b1b1b"/>
        </svg>
        <span>(318) 4207265518</span>
      </li>
      <li class="contact__item">
        <svg class="contact__icon" viewBox="0 0 18 20" aria-hidden="true">
          <circle cx="9" cy="10" r="8" fill="#1b1b1b"/>
          <circle cx="7" cy="8" r="2.5" fill="#ffffff"/>
        </svg>
        <span>www.lumadrift.com</span>
      </li>
    </ul>

    <div class="name-band">
      <svg viewBox="0 0 300 76" width="300" height="76" aria-hidden="true">
        <defs>
          <linearGradient id="bandShade" x1="0" y1="0" x2="1" y2="0">
            <stop offset="0" stop-color="#1c1c1c"/>
            <stop offset="0.35" stop-color="#2e2e2e"/>
            <stop offset="1" stop-color="#4a4a4a"/>
          </linearGradient>
        </defs>
        <polygon points="0,38 60,0 300,0 300,76 60,76" fill="url(#bandShade)"/>
      </svg>
      <div class="name-band__text">
        <p class="name-band__name">ALEX MORAN</p>
        <p class="name-band__title">PRESIDENT</p>
      </div>
    </div>
  </section>

  <section class="card card--back" aria-label="Card back">
    <div class="back-brand">
      <span class="back-brand__name">LUMA</span>
    </div>
    <p class="back-web">LUMADRIFT.COM</p>
  </section>

</main>
</body>
</html>
```